Web Design for a Biotech Consulting Firm

We need a web site design for a new business based in Philadelphia called Verantel Dx. This is a consulting firm that will serve medical diagnostics industry, which is part of the life science/healthcare industry focusing on developing and marketing products that help in early detection, monitoring or management of diseases. Our consulting firm will help medical diagnostic companies to overcome key challenges in designing, evaluating and marketing new products.Our company name is Verantel Dx. Verantel is Latin word for "something" Dx represents diagnostics. The idea behind the name is that we help companies to transform the original, early product ideas ("nothing") into "something"; which is a product with full clinical utility that will help to improve health and well-being.The web site should use the visual feel of the logo (attached), be modern, simple and clean looking and represent creativity, innovation, scientific thinking and progress.
Updates

Wix Design is acceptable

Industry/Entity Type

Biotechnology

Coding

Coded - Design and coding required

Number of Pages Required

1 page

Font styles to use
Sans Serif

Requirements
Must have
• simple, clean look couple of pages
Should not have
• a lot of pages

```html
<!DOCTYPE html>
<html lang="en">
<head>
<meta charset="utf-8">
<title>Verantel Dx</title>
<link rel="stylesheet" href="https://fonts.googleapis.com/css2?family=Montserrat:ital,wght@0,400;0,500;0,600;0,700;1,500&display=swap">
<style>
:root{
  --blue:#2a86ec;
  --blue-dark:#1c6fd1;
  --ink:#1d1d1f;
  --text:#333a44;
  --muted:#8b929b;
  --grey-bg:#f2f2f2;
  --dark:#2b2f35;
  --dark-2:#22252a;
  --panel:#1c1e22;
  --white:#ffffff;
  --line:#d5d8dc;
}
*{box-sizing:border-box;margin:0;padding:0}
html,body{width:1200px;height:5085px;overflow:hidden}
body{position:relative;font-family:"Montserrat",Arial,sans-serif;color:var(--text);background:var(--white)}
.abs{position:absolute}
a{color:inherit;text-decoration:none}

/* header / hero */
.hero{left:0;top:0;width:1200px;height:660px;background:linear-gradient(135deg,#a9c4de 0%,#d6e3f0 45%,#eef3f8 70%,#c9d9ea 100%);clip-path:polygon(0 0,100% 0,100% 575px,50% 660px,0 575px)}
.hero-photo{inset:0;background:radial-gradient(ellipse at 30% 40%,rgba(80,130,190,.55),transparent 60%),radial-gradient(ellipse at 70% 30%,rgba(255,255,255,.6),transparent 55%)}
.topbar{right:0;top:13px;width:520px;height:43px;background:var(--blue);color:var(--white);font-size:14px;display:flex;align-items:center;gap:34px;padding-left:34px;clip-path:polygon(22px 0,100% 0,100% 100%,0 100%)}
.topbar span{display:flex;align-items:center;gap:8px}
.social-dots{display:flex;gap:5px;margin-left:auto;margin-right:24px}
.social-dots i{width:16px;height:16px;border:1.5px solid var(--white);border-radius:50%;display:block}
.logo{display:flex;align-items:center;justify-content:center;border:2px solid var(--blue);font-weight:500;color:var(--ink)}
.logo-header{left:50px;top:42px;width:155px;height:120px;font-size:26px}
.nav{top:88px;right:34px;display:flex;gap:24px;font-size:12px;font-weight:600;color:var(--ink);text-transform:uppercase}
.nav a.active{border:1.5px solid var(--ink);padding:6px 8px;margin-top:-8px}
.hero-title{left:0;width:1200px;top:325px;text-align:center;font-size:34px;font-weight:700;color:#23282f;line-height:1.22}
.btn{display:flex;align-items:center;justify-content:center;background:var(--blue);color:var(--white);font-weight:600;text-transform:uppercase;border-radius:6px}
.hero-btn{left:478px;top:432px;width:244px;height:48px;font-size:18px}

/* section title */
.sec-title{left:0;width:1200px;display:flex;justify-content:center}
.sec-title h2{font-size:28px;font-weight:700;color:var(--ink);padding:18px 18px 14px;border-left:3px solid var(--blue);border-top:3px solid var(--blue);position:relative;background:inherit}
.sec-title h2::after{content:"";position:absolute;left:-3px;bottom:-3px;width:30px;height:3px;background:var(--blue)}
.sec-title h2 em{font-style:normal;font-weight:500;color:var(--blue)}
.sec-title.on-dark h2{color:var(--white)}

/* about */
.about-text{left:100px;top:865px;width:1000px;text-align:center;font-size:16px;line-height:1.5;color:var(--text)}
.about-btn{left:512px;top:990px;width:178px;height:42px;font-size:12px}

/* services */
.services{left:0;top:1126px;width:1200px;height:595px;background:var(--grey-bg)}
.service{top:1330px;width:305px}
.service .photo{height:188px}
.service h3{margin-top:30px;font-size:16px;font-weight:500;color:var(--blue)}
.service p{font-size:15px;line-height:1.4;color:var(--ink);margin-top:4px}
.arrow-btn{width:30px;height:30px;border-radius:50%;background:var(--blue);display:flex;align-items:center;justify-content:center}

/* clients */
.clients{left:0;top:1930px;width:1200px;display:flex;justify-content:center;gap:62px;font-size:34px;font-weight:700;color:#b2b5b9}

/* news */
.news{left:0;top:2074px;width:1200px;height:1091px;background:radial-gradient(ellipse at 60% 20%,#4a4f57,transparent 60%),linear-gradient(180deg,var(--dark),var(--dark-2));clip-path:polygon(0 0,100% 0,100% 1002px,50% 1091px,0 1002px)}
.news-card{background:var(--panel);color:var(--white);padding:28px 26px}
.news-card .date{color:var(--blue);font-size:16px;font-weight:500}
.news-card p{font-size:17px;line-height:1.4;margin-top:4px}
.news-card .go{margin-top:12px;width:26px;height:26px;border:2px solid var(--blue);border-radius:50%;display:flex;align-items:center;justify-content:center}
.view-all{left:905px;top:2702px;width:221px;height:275px;background:var(--blue);color:var(--white);font-size:26px;font-weight:500;text-align:center;display:flex;align-items:center;justify-content:center;line-height:1.3}

/* testimonials */
.quote{background:var(--white);border:1.5px solid var(--line);border-radius:8px;padding:22px 26px;font-size:14px;line-height:1.75;color:var(--text)}
.quote::after{content:"";position:absolute;left:50px;bottom:-14px;width:24px;height:24px;background:var(--white);border-right:1.5px solid var(--line);border-bottom:1.5px solid var(--line);transform:rotate(45deg)}
.avatar{width:92px;height:92px;border-radius:50%;border:3px solid var(--blue);background:radial-gradient(circle at 50% 40%,#f3d9c4,#c9a88c 70%)}
.person{font-size:19px;font-weight:500;font-style:italic;color:var(--ink)}
.dots{left:0;width:1200px;top:3790px;display:flex;justify-content:center;gap:5px}
.dots i{width:14px;height:14px;border:1.5px solid var(--muted);border-radius:50%;display:block}
.dots i.on{background:var(--muted)}

/* contact */
.contact{left:0;top:3897px;width:1200px;height:546px;background:var(--grey-bg)}
.field{background:var(--white);height:49px;padding:14px 16px;font-size:16px;color:var(--ink)}
.field-msg{left:76px;top:4161px;width:745px;height:130px}
.submit{left:358px;top:4311px;width:178px;height:36px;font-size:13px}
.info{left:872px;font-size:17px;color:var(--ink);line-height:1.45;display:flex;gap:12px}
.info svg{flex:none;margin-top:2px}

/* footer */
.footer{left:0;top:4443px;width:1200px;height:590px;background:linear-gradient(180deg,#2e3239,#23262b)}
.footer-peak{left:0;top:4443px;width:1200px;height:140px;background:#3c4149;clip-path:polygon(0 0,100% 0,50% 100%)}
.logo-footer{left:526px;top:4600px;width:125px;height:123px;color:var(--white);font-size:26px}
.foot-col{top:4790px;font-size:12px;color:#e5e7ea;line-height:1.55}
.foot-col h4{color:var(--blue);font-size:12px;font-weight:600;text-transform:uppercase;margin-bottom:22px}
.foot-col .social{display:flex;align-items:center;gap:14px;margin-bottom:18px}
.foot-col .social i{width:24px;height:24px;border-radius:50%;background:var(--blue);display:block}
.email-in{margin-top:16px;width:260px;height:30px;background:var(--white);border-radius:15px;color:var(--ink);padding:7px 16px;font-size:12px}
.sub-btn{margin-top:12px;width:130px;height:28px;border-radius:14px;font-size:12px}
.copyright{left:0;top:5033px;width:1200px;height:52px;background:var(--white);text-align:center;font-size:12px;line-height:52px;color:var(--ink);text-transform:uppercase}
</style>
</head>
<body>

<header>
  <div class="abs hero">
    <div class="abs hero-photo" role="img" aria-label="Doctor in blue scrubs holding a tablet with a glowing diagnostic interface"></div>
  </div>
  <div class="abs topbar">
    <span><svg width="16" height="16" viewBox="0 0 24 24" fill="none" stroke="#fff" stroke-width="2"><path d="M5 3h4l2 5-3 2a11 11 0 0 0 6 6l2-3 5 2v4a2 2 0 0 1-2 2A17 17 0 0 1 3 5a2 2 0 0 1 2-2z"/></svg>1800.555.0199</span>
    <span><svg width="16" height="16" viewBox="0 0 24 24" fill="none" stroke="#fff" stroke-width="2"><rect x="3" y="5" width="18" height="14" rx="2"/><path d="M3 7l9 6 9-6"/></svg>info@verantelconsult.com</span>
    <span class="social-dots"><i></i><i></i><i></i></span>
  </div>
  <div class="abs logo logo-header">Verantel Dx</div>
  <nav class="abs nav">
    <a class="active">Home</a><a>About</a><a>Services</a><a>Clients</a><a>News</a><a>Testimonials</a><a>Contact</a>
  </nav>
  <h1 class="abs hero-title">Helping Medical Diagnostic Companies to Overcome Key<br>Challenges in Designing, Evaluating and Marketing New Products</h1>
  <a class="abs btn hero-btn">Learn More</a>
</header>

<section class="about">
  <div class="abs sec-title" style="top:750px;background:var(--white)"><h2>ABOUT Verantel <em>Dx</em></h2></div>
  <p class="abs about-text">Lorem ipsum dolor sit amet, consectetuer adipiscing elit, sed diam nonummy nibh euismod tincidunt ut laoreet dolore magna aliquam erat volutpat. Ut wisi enim ad minim veniam, quis nostrud exerci tation ullamcorper suscipit lobortis nisl ut aliquip ex ea commodo consequat. Duis autem veleum iriure dolor in hendrerit in vul putate velit esse molestie consequat, vel illum dolore eu feugiat nulla facilisis at vero eros et accumsan.</p>
  <a class="abs btn about-btn">Learn More</a>
</section>

<section>
  <div class="abs services"></div>
  <div class="abs sec-title" style="top:1220px;background:var(--grey-bg)"><h2>OUR <em>Services</em></h2></div>
  <div class="abs arrow-btn" style="left:59px;top:1411px"><svg width="14" height="14" viewBox="0 0 24 24" fill="none" stroke="#fff" stroke-width="3"><path d="M20 12H5M11 5l-7 7 7 7"/></svg></div>
  <div class="abs arrow-btn" style="left:1111px;top:1411px"><svg width="14" height="14" viewBox="0 0 24 24" fill="none" stroke="#fff" stroke-width="3"><path d="M4 12h15M13 5l7 7-7 7"/></svg></div>
  <article class="abs service" style="left:122px">
    <div class="photo" role="img" aria-label="Rows of test tubes filled with blue liquid" style="background:linear-gradient(180deg,#cfe6f2,#3aa9d8 70%,#1f6e9a)"></div>
    <h3>New Product Design</h3>
    <p>Lorem ipsum dolor sit amet, con sectetuer adipiscing elit, sed diam nonummy nibh euismod.</p>
  </article>
  <article class="abs service" style="left:447px">
    <div class="photo" role="img" aria-label="Laboratory microscope in grey tones" style="background:linear-gradient(180deg,#e8eaec,#9ba1a8 60%,#3d4147)"></div>
    <h3>New Product Evaluation</h3>
    <p>Lorem ipsum dolor sit amet, con sectetuer adipiscing elit, sed diam nonummy nibh euismod.</p>
  </article>
  <article class="abs service" style="left:770px">
    <div class="photo" role="img" aria-label="Businessman standing on a hill under a bright sky" style="background:linear-gradient(180deg,#f4f1e6 0%,#e6dcc3 55%,#8a6a45 75%,#4d3b28)"></div>
    <h3>Product Marketing</h3>
    <p>Lorem ipsum dolor sit amet, con sectetuer adipiscing elit, sed diam nonummy nibh euismod.</p>
  </article>
</section>

<section>
  <div class="abs sec-title" style="top:1810px;background:var(--white)"><h2>OUR <em>Clients</em></h2></div>
  <div class="abs clients"><span>ROVANT</span><span>WELLO</span><span>GENTRA</span><span>clearForm</span><span>BRAVANCE</span></div>
</section>

<section>
  <div class="abs news" role="img" aria-label="Dimmed background photo of a laboratory workspace"></div>
  <div class="abs sec-title on-dark" style="top:2168px"><h2 style="background:transparent">Latest <em>News</em></h2></div>
  <div class="abs" role="img" aria-label="Doctor using a tablet showing medical scans" style="left:74px;top:2275px;width:416px;height:417px;background:linear-gradient(135deg,#f5f7f9,#d4e0ea 55%,#6a9cc4)"></div>
  <article class="abs news-card" style="left:498px;top:2275px;width:628px;height:186px">
    <div class="date">January 03, 2019</div>
    <p>Lorem ipsum dolor sit amet, consectetuer adipiscing elit. Sed diam nonummy nibh euismod tincidunt ut laoreet dolore magna aliquam erat volutpat.</p>
    <div class="go"><svg width="12" height="12" viewBox="0 0 24 24" fill="none" stroke="#2a86ec" stroke-width="3"><path d="M4 12h15M13 5l7 7-7 7"/></svg></div>
  </article>
  <article class="abs news-card" style="left:498px;top:2471px;width:336px;height:221px">
    <div class="date">February 24, 2019</div>
    <p>Lorem ipsum dolor sit amet. Sed diam nonummy nibh euis mod tincidunt ut laoreet dolore.</p>
    <div class="go"><svg width="12" height="12" viewBox="0 0 24 24" fill="none" stroke="#2a86ec" stroke-width="3"><path d="M4 12h15M13 5l7 7-7 7"/></svg></div>
  </article>
  <div class="abs" role="img" aria-label="Two colleagues reviewing documents at a desk" style="left:841px;top:2471px;width:285px;height:221px;background:linear-gradient(135deg,#eef0f2,#b9c2cc 60%,#4b5561)"></div>
  <article class="abs news-card" style="left:74px;top:2702px;width:295px;height:275px">
    <div class="date">March 19, 2019</div>
    <p>Lorem ipsum dolor sit am. Sed diam nonummy nibh euismod tincidunt ut.</p>
    <div class="go"><svg width="12" height="12" viewBox="0 0 24 24" fill="none" stroke="#2a86ec" stroke-width="3"><path d="M4 12h15M13 5l7 7-7 7"/></svg></div>
  </article>
  <div class="abs" role="img" aria-label="Finger touching a glowing blue data screen" style="left:369px;top:2702px;width:526px;height:275px;background:radial-gradient(ellipse at 55% 60%,#c25bd0,transparent 45%),linear-gradient(135deg,#0c1a3a,#1e4d9a 60%,#0a1530)"></div>
  <svg class="abs" style="left:369px;top:2824px" width="16" height="32"><polygon points="0,0 16,16 0,32" fill="#1c1e22"/></svg>
  <a class="abs view-all">VIEW<br>ALL NEWS</a>
</section>

<section>
  <div class="abs sec-title" style="top:3256px;background:var(--white)"><h2>Testimonials</h2></div>
  <blockquote class="abs quote" style="left:92px;top:3368px;width:518px;height:181px">Lorem ipsum dolor sit amet, consectetur adipiscing elit, sed do eiusmod tempor incididunt ut labore et dolore magna aliqua. Ut enim ad minim veniam, quis nostrud exercitation ullamco laboris nisi ut aliquip ex. Duis aute irure dolor in reprehenderit in voluptate velit esse.</blockquote>
  <div class="abs avatar" role="img" aria-label="Portrait of client Helen Marsh" style="left:106px;top:3576px"></div>
  <div class="abs person" style="left:221px;top:3610px">Helen Marsh</div>
  <blockquote class="abs quote" style="left:592px;top:3424px;width:519px;height:181px">Lorem ipsum dolor sit amet, consectetur adipiscing elit, sed do eiusmod tempor incididunt ut labore et dolore magna aliqua. Ut enim ad minim veniam, quis nostrud exercitation ullamco laboris nisi ut aliquip ex. Duis aute irure dolor in reprehenderit in voluptate velit esse.</blockquote>
  <div class="abs avatar" role="img" aria-label="Portrait of client Laura Pennick" style="left:605px;top:3630px"></div>
  <div class="abs person" style="left:709px;top:3665px">Laura Pennick</div>
  <div class="abs dots"><i class="on"></i><i></i><i></i><i></i></div>
</section>

<section>
  <div class="abs contact"></div>
  <div class="abs" style="left:330px;top:3991px"><div class="sec-title" style="position:static;width:auto;background:var(--grey-bg)"><h2>Send <em>a Message</em></h2></div></div>
  <div class="abs" style="left:923px;top:3991px"><div class="sec-title" style="position:static;width:auto;background:var(--grey-bg)"><h2>Contact <em>Us</em></h2></div></div>
  <div class="abs field" style="left:76px;top:4100px;width:237px">Your Name</div>
  <div class="abs field" style="left:330px;top:4100px;width:237px">Your Email</div>
  <div class="abs field" style="left:585px;top:4100px;width:236px">Your Subject</div>
  <div class="abs field field-msg">Message</div>
  <a class="abs btn submit">Submit</a>
  <div class="abs info" style="top:4100px"><svg width="20" height="20" viewBox="0 0 24 24" fill="none" stroke="#1d1d1f" stroke-width="2"><path d="M12 22s7-7 7-12a7 7 0 0 0-14 0c0 5 7 12 7 12z"/><circle cx="12" cy="10" r="2.5"/></svg><div>Verantel Dx<br>48 Market Lane<br>Suite #210<br>Philadelphia, PA 19106</div></div>
  <div class="abs info" style="top:4233px"><svg width="20" height="20" viewBox="0 0 24 24" fill="none" stroke="#1d1d1f" stroke-width="2"><circle cx="12" cy="12" r="10"/><path d="M9 7h2l1 3-1.5 1a6 6 0 0 0 3 3L15 13l3 1v2a1 1 0 0 1-1 1A9 9 0 0 1 8 8a1 1 0 0 1 1-1z"/></svg><div>1800-555-0199</div></div>
  <div class="abs info" style="top:4286px"><svg width="20" height="20" viewBox="0 0 24 24" fill="none" stroke="#1d1d1f" stroke-width="2"><circle cx="12" cy="12" r="10"/><circle cx="12" cy="12" r="3.5"/></svg><div>info@verantelconsult.com</div></div>
</section>

<footer>
  <div class="abs footer" role="img" aria-label="Dimmed photo of laboratory equipment"></div>
  <div class="abs footer-peak"></div>
  <div class="abs logo logo-footer">Verantel Dx</div>
  <div class="abs foot-col" style="left:158px">
    <h4>Quick Links</h4>
    Home<br>About<br>Services<br>Clients<br>News<br>Testimonials<br>Contact
  </div>
  <div class="abs foot-col" style="left:348px">
    <h4>Services</h4>
    New Product Design<br>New Product Evaluation<br>Product Marketing
  </div>
  <div class="abs foot-col" style="left:587px">
    <h4>Follow Us</h4>
    <div class="social"><i></i>Friendnet</div>
    <div class="social"><i></i>Chirper</div>
    <div class="social"><i></i>Linkwork</div>
  </div>
  <div class="abs foot-col" style="left:790px;width:270px">
    <h4>Newsletter Sign Up</h4>
    Register your email address to get<br>more information about us
    <div class="email-in">Email Address</div>
    <div class="btn sub-btn">Subscribe</div>
  </div>
  <div class="abs copyright">Copyright © 2019 Verantel Dx. All rights reserved.</div>
</footer>

</body>
</html>
```